Website Design for Architecture Practice

I need a home page and one sidebar/content page for an Architecture practice delivered in PSD.

This archictecture practice specialises in one-off, high end homes and commercial properties (restaurant) heavily influenced by Edmund Harcourt Vale, particularly his work on the Pellworth Museum

I am looking for a home page, and a generic content page where we can outline our services, and showcase our homes.

http://journals.kestrelhill.edu.au/artnotes/Pellworth%20Quayside%202.jpg

Target Market(s)

30-70yr old (typically wealthy) property buyers, developers and investors

Industry/Entity Type

Architecture

Number of Pages Required

2 page

Font styles to use
Serif
Sans Serif

Requirements
Must have
• Home page design
• a Content Page design (ie, top nav with sidebar)
Nice to have
• Use any Edmund Harcourt Vale images you can find via google etc as placeholders for our own photography (ie they don't need to be licensed as we will be replacing with our own commissioned photography). Full color preferred but feel free to experiment with treating any images as you see fit.

```html
<!DOCTYPE html>
<html lang="en">
<head>
<meta charset="utf-8">
<title>Crestline Studio</title>
<link href="https://fonts.googleapis.com/css2?family=Open+Sans:wght@400;600;700&display=swap" rel="stylesheet">
<style>
:root{
  --teal:#4ec5d2;
  --teal-dark:#3aaebb;
  --ink:#2b2b2b;
  --night:#1f1f1f;
  --footer:#262626;
  --paper:#f3f3f3;
  --muted:#8a8a8a;
  --white:#ffffff;
}
*{box-sizing:border-box;margin:0;padding:0}
html,body{width:736px;height:1200px;overflow:hidden}
body{font-family:"Open Sans",Arial,sans-serif;background:var(--paper);color:var(--ink);position:relative}
.wrap{width:576px;margin:0 auto;position:relative}

.site-header{position:absolute;top:0;left:0;width:736px;height:40px;background:rgba(20,20,20,.92);z-index:2}
.site-header .wrap{display:flex;justify-content:space-between;align-items:center;height:40px}
.brand{color:var(--white);font-weight:700;font-size:15px}
.main-nav{display:flex;gap:26px;font-size:10px;color:#cfcfcf}
.main-nav .active{color:var(--white);font-weight:700}

.hero{position:absolute;top:0;left:0;width:736px;height:362px;
  background:linear-gradient(160deg,#24301e 0%,#4a5a33 30%,#8a8470 50%,#5e5b4d 65%,#2f3a26 85%,#1e2418 100%)}
.hero-tagline{position:absolute;top:158px;left:80px;width:250px;color:var(--white);font-weight:700;font-size:11.5px;line-height:15px;text-shadow:0 1px 2px rgba(0,0,0,.6)}
.hero-dots{position:absolute;top:322px;left:615px;display:flex;gap:5px}
.hero-dots span{width:6px;height:6px;border-radius:50%;background:rgba(255,255,255,.6)}
.hero-dots span.on{background:var(--white)}

.specialities{position:absolute;top:362px;left:0;width:736px;height:230px;background:var(--paper);border-bottom:1px solid #e2e2e2}
.specialities .wrap{display:flex;justify-content:space-between;padding-top:42px}
.speciality{width:140px;text-align:center}
.speciality .badge{width:90px;height:90px;margin:0 auto;border-radius:50%;border:4px solid var(--teal);background:#3a3a3a;display:flex;align-items:center;justify-content:center;box-shadow:0 0 0 4px #e4e4e4}
.speciality h3{margin-top:20px;font-weight:400;font-size:13px;color:#444}

.welcome{position:absolute;top:592px;left:0;width:736px;height:193px;text-align:center}
.welcome h1{margin-top:24px;font-weight:400;font-size:22px;color:#444}
.welcome h1 em{font-style:normal;color:var(--teal-dark)}
.welcome p{width:576px;margin:14px auto 0;font-size:6.5px;line-height:11px;color:var(--muted)}
.btn{display:inline-block;margin-top:18px;padding:4px 12px;background:#d5d5d5;border:1px solid #c4c4c4;font-size:7px;color:#555}

.showcase{position:absolute;top:785px;left:0;width:736px;height:270px;background:var(--teal)}
.showcase .wrap{display:flex;gap:24px;padding-top:20px}
.facilities{width:190px}
.section-title{color:var(--white);font-weight:700;font-size:15px;margin-bottom:14px}
.section-title span{font-weight:400}
.facilities li{list-style:none;display:flex;align-items:center;gap:7px;color:var(--white);font-size:6.5px;margin-bottom:11px}
.facilities li svg{flex:none}
.gallery{flex:1}
.gallery-head{display:flex;justify-content:space-between;align-items:baseline}
.view-all{color:var(--white);font-size:7px;text-decoration:underline}
.gallery-frame{background:var(--white);padding:6px;display:grid;grid-template-columns:repeat(4,1fr);gap:5px}
.thumb{height:66px}
.t1{background:linear-gradient(135deg,#9fb3c3,#c9c2ae,#6d7a82)}
.t2{background:linear-gradient(135deg,#2f4a25,#76866a,#3b3f2e)}
.t3{background:linear-gradient(135deg,#6c8fae,#b8b6a8,#4a5d6c)}
.t4{background:linear-gradient(135deg,#8eb3d4,#d8d2c4,#6a6a5c)}
.t5{background:linear-gradient(135deg,#3c5b2c,#8e9a7a,#2a3320)}
.t6{background:linear-gradient(135deg,#51687a,#a9a08a,#2e3b43)}
.t7{background:linear-gradient(135deg,#7b5c3e,#c5b092,#4d3b2a)}
.t8{background:linear-gradient(135deg,#6a8fb8,#e2ddd0,#a35c4a)}

.site-footer{position:absolute;top:1055px;left:0;width:736px;height:125px;background:var(--footer);color:#bdbdbd}
.site-footer .wrap{display:flex;justify-content:space-between;padding-top:16px}
.site-footer h4{color:var(--white);font-size:7.5px;font-weight:700;margin-bottom:10px}
.site-footer h4 span{font-weight:400}
.quick-links li{list-style:none;font-size:6.5px;margin-bottom:5px}
.contact-list li{list-style:none;display:flex;gap:6px;font-size:6.5px;margin-bottom:7px;line-height:9px}
.contact-list .ico{width:10px;height:10px;border-radius:50%;background:#4a4a4a;flex:none;display:flex;align-items:center;justify-content:center}
.newsletter p{font-size:6px;width:120px;line-height:8px;margin-bottom:5px}
.field{width:118px;height:11px;background:var(--white);margin-bottom:4px;font-size:5.5px;color:#999;padding:2px 3px}
.subscribe{display:inline-block;background:var(--teal);color:var(--white);font-size:6px;padding:2px 6px}
.social li{list-style:none;display:flex;align-items:center;gap:6px;font-size:6.5px;margin-bottom:7px;color:#ddd;font-weight:600}
.social .dot{width:14px;height:14px;border-radius:50%;background:#3d3d3d}

.legal{position:absolute;top:1180px;left:0;width:736px;height:20px;background:var(--night);color:#9a9a9a;font-size:6.5px}
.legal .wrap{display:flex;justify-content:space-between;align-items:center;height:20px}
</style>
</head>
<body>

<div class="hero" role="img" aria-label="Photograph of a cantilevered concrete house above a waterfall in woodland"></div>

<header class="site-header">
  <div class="wrap">
    <div class="brand">Crestline Studio</div>
    <nav class="main-nav">
      <span class="active">Home</span><span>About</span><span>Services</span><span>Gallery</span><span>Contact</span>
    </nav>
  </div>
</header>

<p class="hero-tagline">We Are An Architecture Business / Practice That Specialises In One-off, High End Homes And Commercial Properties</p>
<div class="hero-dots"><span class="on"></span><span></span><span></span><span></span></div>

<section class="specialities">
  <div class="wrap">
    <div class="speciality">
      <div class="badge">
        <svg width="40" height="40" viewBox="0 0 40 40"><circle cx="20" cy="20" r="12" fill="none" stroke="var(--teal)" stroke-width="7" stroke-dasharray="5 4"/><circle cx="20" cy="20" r="9" fill="var(--teal)"/><circle cx="20" cy="20" r="4" fill="#3a3a3a"/></svg>
      </div>
      <h3>One-off</h3>
    </div>
    <div class="speciality">
      <div class="badge">
        <svg width="44" height="36" viewBox="0 0 44 36" fill="none" stroke="#fff" stroke-width="2"><rect x="4" y="10" width="36" height="24"/><path d="M2 10h40M14 4h16v6"/><rect x="9" y="15" width="6" height="5"/><rect x="19" y="15" width="6" height="5"/><rect x="29" y="15" width="6" height="5"/><rect x="19" y="24" width="6" height="10"/></svg>
      </div>
      <h3>High End Homes</h3>
    </div>
    <div class="speciality">
      <div class="badge">
        <svg width="26" height="46" viewBox="0 0 26 46" fill="#9a9a9a"><rect x="6" y="8" width="14" height="38"/><rect x="11" y="0" width="4" height="8"/><g fill="#5a5a5a"><rect x="8" y="12" width="3" height="3"/><rect x="15" y="12" width="3" height="3"/><rect x="8" y="20" width="3" height="3"/><rect x="15" y="20" width="3" height="3"/><rect x="8" y="28" width="3" height="3"/><rect x="15" y="28" width="3" height="3"/></g></svg>
      </div>
      <h3>Commercial Properties</h3>
    </div>
  </div>
</section>

<section class="welcome">
  <h1>Welcome to <em>Crestline Studio</em></h1>
  <p>Each of our homes is drawn from the site itself, shaped by light, water, stone and the slope of the land. We work closely with every client from the first sketch to the final handover, bringing craft, patience and honest materials to each project. Our studio designs private residences and restaurants that sit quietly within their setting, with generous terraces, long horizontal lines and rooms that open to the landscape beyond. We believe good architecture should feel calm, lasting and personal, and we take on a small number of commissions each year.</p>
  <span class="btn">Read More</span>
</section>

<section class="showcase">
  <div class="wrap">
    <div class="facilities">
      <h2 class="section-title">Our <span>Facilities</span></h2>
      <ul>
        <li><svg width="8" height="8" viewBox="0 0 8 8"><path d="M1 4l2 2 4-5" fill="none" stroke="#fff" stroke-width="1.4"/></svg>Site visits and feasibility studies</li>
        <li><svg width="8" height="8" viewBox="0 0 8 8"><path d="M1 4l2 2 4-5" fill="none" stroke="#fff" stroke-width="1.4"/></svg>Concept design and planning advice</li>
        <li><svg width="8" height="8" viewBox="0 0 8 8"><path d="M1 4l2 2 4-5" fill="none" stroke="#fff" stroke-width="1.4"/></svg>Detailed drawings and models</li>
        <li><svg width="8" height="8" viewBox="0 0 8 8"><path d="M1 4l2 2 4-5" fill="none" stroke="#fff" stroke-width="1.4"/></svg>Interior and landscape design</li>
        <li><svg width="8" height="8" viewBox="0 0 8 8"><path d="M1 4l2 2 4-5" fill="none" stroke="#fff" stroke-width="1.4"/></svg>Builder selection and tendering</li>
        <li><svg width="8" height="8" viewBox="0 0 8 8"><path d="M1 4l2 2 4-5" fill="none" stroke="#fff" stroke-width="1.4"/></svg>Construction oversight and handover</li>
      </ul>
    </div>
    <div class="gallery">
      <div class="gallery-head">
        <h2 class="section-title">Our <span>Gallery</span></h2>
        <span class="view-all">View All</span>
      </div>
      <div class="gallery-frame">
        <div class="thumb t1" role="img" aria-label="Curved metal-clad museum on a river quayside"></div>
        <div class="thumb t2" role="img" aria-label="Stone house among green trees"></div>
        <div class="thumb t3" role="img" aria-label="Long low house with flat roof"></div>
        <div class="thumb t4" role="img" aria-label="Modern villa beneath a blue sky"></div>
        <div class="thumb t5" role="img" aria-label="Cantilevered house over a stream in forest"></div>
        <div class="thumb t6" role="img" aria-label="Concrete building at dusk"></div>
        <div class="thumb t7" role="img" aria-label="Timber interior with built-in seating"></div>
        <div class="thumb t8" role="img" aria-label="Prairie style house with red roof"></div>
      </div>
    </div>
  </div>
</section>

<footer class="site-footer">
  <div class="wrap">
    <div class="quick-links">
      <h4>QUICK <span>LINKS</span></h4>
      <ul><li>Home</li><li>About</li><li>Services</li><li>Gallery</li><li>Contact</li></ul>
    </div>
    <div class="contact-list">
      <h4>CONTACT <span>ADDRESS</span></h4>
      <ul>
        <li><span class="ico"><svg width="6" height="7" viewBox="0 0 6 7"><path d="M3 7C1 4.5 .5 3.5.5 2.5a2.5 2.5 0 015 0C5.5 3.5 5 4.5 3 7z" fill="#ccc"/></svg></span>Studio 4, 18 Quarry Lane<br>Millbrook Hills, 2208</li>
        <li><span class="ico"><svg width="6" height="6" viewBox="0 0 6 6"><path d="M1 0l1.3 1.6-.6 1a3 3 0 001.7 1.7l1-.6L6 5 5 6C2 6 0 4 0 1z" fill="#ccc"/></svg></span>(+)123-456-7890</li>
        <li><span class="ico"><svg width="6" height="5" viewBox="0 0 6 5"><rect width="6" height="5" fill="#ccc"/><path d="M0 0l3 2.5L6 0" fill="none" stroke="#4a4a4a" stroke-width=".7"/></svg></span>studio@crestlinestudio.net</li>
      </ul>
    </div>
    <div class="newsletter">
      <h4>NEWSLETTER <span>SIGNUP</span></h4>
      <p>Sign up with us to get updates on our latest projects</p>
      <div class="field">Your Name</div>
      <div class="field">Your Email</div>
      <span class="subscribe">Subscribe</span>
    </div>
    <div class="social">
      <h4>SOCIAL <span>CONNECT</span></h4>
      <ul>
        <li><span class="dot"></span>COMMONS</li>
        <li><span class="dot"></span>PHOTOSTREAM</li>
        <li><span class="dot"></span>NEWSLINE</li>
      </ul>
    </div>
  </div>
</footer>

<div class="legal">
  <div class="wrap">
    <span>Copyright 2013 Crestline Studio. All Rights Reserved</span>
    <span>Terms and Conditions &nbsp;|&nbsp; Privacy Policy</span>
  </div>
</div>

</body>
</html>
```